Specialist Recruitment Process Outsourcing (RPO) company needs a modern, sleek website

We need a website which showcases our service offering, describes our onshore and offshore options. Our service is basically building teams of recruiters who become the outsourced (but in-house) recruiter for that specific client. Our logo colours include a light, bright green and a dark/midnight blue. This company will be targeting companies who need help with recruitment in technology, finance, engineering and other white collar industries. We are looking for a look and feeling that communicates cutting edge technology with a bright, energetic appeal. I will include some logo design files to work with.

Target Market(s)

Businesses: start ups who need to grow their staff, SMEs with regular recruitment needs, and larger businesses

Industry/Entity Type

Recruitment

Coding

Coded - Design and coding required

Number of Pages Required

4 page

Font styles to use
Sans Serif

Requirements
Must have
• Landing page should be highly visual, either with dynamic image or scrolling stills accompanies by our core service offering, values, and benefits.

A Services page will allows more detail about what we do, with a call to action.

A User Stories page will showcase some examples of how our services will help certain types of businesses.

Onshore/Offshore page will breakdown the benefits of both approaches and how combinations can work well.

Should fit the colour theming of our logo (files uploaded).

Nice to have
• Imagery can be both around business and people. We are looking for more of a "startup" feel than a corporate-y feel.

```html
<!DOCTYPE html>
<html lang="en">
<head>
<meta charset="utf-8">
<title>Crewline — Recruitment Process Outsourcing</title>
<link href="https://fonts.googleapis.com/css2?family=Montserrat:wght@400;500;600&family=Roboto:wght@400;500&display=swap" rel="stylesheet">
<style>
:root{
  --blue:#0a3fbf;
  --green:#0bcc2a;
  --ink:#1d1d1d;
  --text:#2b2b2b;
  --black:#060606;
  --white:#ffffff;
}
*{margin:0;padding:0;box-sizing:border-box}
html,body{width:1200px;height:2506px;overflow:hidden;background:var(--white)}
body{position:relative;font-family:"Roboto",Arial,sans-serif;color:var(--text)}
.abs{position:absolute}
.brand{font-family:"Montserrat",Arial,sans-serif;font-weight:600;letter-spacing:.28em;color:var(--ink)}
.site-header .brand{left:90px;top:80px;font-size:15px;display:flex;align-items:center;gap:10px;line-height:18px}
.brand .mark{width:11px;height:11px;background:var(--ink)}
.top-links{top:32px;font-family:"Montserrat",sans-serif;font-size:16px;color:var(--blue);display:flex;align-items:center;gap:8px}
.nav{top:82px;left:430px;right:90px;display:flex;justify-content:space-between;font-family:"Montserrat",sans-serif;font-size:14.5px;font-weight:500;letter-spacing:.06em;color:var(--ink)}
.nav .active{color:var(--blue)}
.hero{left:0;top:118px;width:1200px;height:688px}
.hero-title{left:760px;top:300px;width:350px;text-align:center;font-family:"Montserrat",sans-serif;font-weight:600;font-size:38px;line-height:46px;letter-spacing:.3em;color:var(--white)}
.btn{background:var(--green);color:var(--white);font-family:"Roboto",sans-serif;font-weight:500;font-size:16px;display:flex;align-items:center;justify-content:center;letter-spacing:-.01em}
.hero .hero-btn{left:845px;top:378px;width:176px;height:49px}
.dots{left:888px;top:538px;display:flex;gap:15px}
.dots span{width:9px;height:9px;border-radius:50%;background:var(--green)}
.dots span.on{background:var(--blue)}
.section-title{font-family:"Montserrat",sans-serif;font-weight:600;color:var(--ink);letter-spacing:.05em;line-height:1.1}
.offer-title{left:0;width:1200px;top:884px;text-align:center;font-size:46px}
.cards{left:89px;top:960px;display:flex;gap:10px}
.card{width:197px;height:204px;background:var(--white);box-shadow:0 0 8px rgba(0,0,0,.13);padding:32px 16px 0}
.card svg{width:58px;height:58px;display:block}
.card h3{margin-top:30px;font-family:"Montserrat",sans-serif;font-weight:500;font-size:22px;line-height:31px;color:var(--ink)}
.frame{border:3px solid var(--blue)}
.photo{display:block}
.feature-title{font-size:46px}
.feature-text{font-size:15px;line-height:35px;text-align:justify;width:524px}
.feature .btn{width:176px;height:49px}
.footer{left:0;top:2130px;width:1200px;height:376px;background:var(--black);color:var(--white)}
.footer .brand{position:absolute;left:0;width:1200px;top:188px;text-align:center;font-size:24px;color:var(--white)}
.footer-nav{left:0;width:1200px;top:245px;display:flex;justify-content:center;gap:20px;font-family:"Montserrat",sans-serif;font-weight:500;font-size:15px;letter-spacing:.08em}
.social{left:0;width:1200px;top:303px;display:flex;justify-content:center;gap:26px}
.social span{width:12px;height:12px;border-radius:50%;background:var(--white)}
.copy{left:0;width:1200px;top:336px;text-align:center;font-size:13.5px}
</style>
</head>
<body>
<header class="site-header">
  <div class="abs brand"><span class="mark"></span>CREWLINE</div>
  <div class="abs top-links" style="left:770px">
    <svg width="14" height="15" viewBox="0 0 14 15"><circle cx="7" cy="4" r="3.6" fill="#0a3fbf"/><path d="M0 15c0-5 3-7 7-7s7 2 7 7z" fill="#0a3fbf"/></svg>Login</div>
  <div class="abs top-links" style="left:934px">
    <svg width="17" height="13" viewBox="0 0 17 13"><rect width="17" height="13" rx="1" fill="#0a3fbf"/><path d="M1 1l7.5 6L16 1" stroke="#fff" stroke-width="1.5" fill="none"/></svg>info@crewline.com</div>
  <nav class="abs nav"><span class="active">HOME</span><span>SERVICE</span><span>USER STORIES</span><span>ONSHORE/OFFSHORE</span><span>CONTACT</span></nav>
</header>

<section class="abs hero">
  <svg class="abs" width="1200" height="688" viewBox="0 0 1200 688" role="img" aria-label="Business team photo with hexagon collage of handshake, networked city and people at work">
    <defs>
      <linearGradient id="heroGrad" x1="0" y1="0" x2="1" y2="1">
        <stop offset="0" stop-color="#b9ccd6"/><stop offset=".5" stop-color="#6f94aa"/><stop offset="1" stop-color="#3f6a86"/>
      </linearGradient>
    </defs>
    <path d="M0 0H1200V607H915L603 688 420 640 0 607Z" fill="url(#heroGrad)"/>
    <g fill="#2c5578" stroke="#fff" stroke-width="10">
      <polygon points="215,345 290,205 440,205 515,345 440,485 290,485"/>
      <polygon points="20,210 65,125 170,125 215,210 170,295 65,295"/>
      <polygon points="225,95 255,42 325,42 355,95 325,148 255,148"/>
      <polygon points="-20,470 25,385 130,385 175,470 130,555 25,555"/>
      <polygon points="608,308 638,255 700,255 730,308 700,361 638,361"/>
      <polygon points="510,590 548,522 633,522 671,590 633,658 548,658"/>
      <polygon points="755,500 780,456 838,456 863,500 838,544 780,544"/>
    </g>
    <polygon points="195,345 278,190 452,190 535,345 452,500 278,500" fill="none" stroke="#fff" stroke-width="3"/>
  </svg>
  <div class="abs hero-title">CREWLINE</div>
  <div class="abs btn hero-btn">GET STARTED</div>
  <div class="abs dots"><span></span><span class="on"></span><span></span><span></span></div>
</section>

<h2 class="abs section-title offer-title">SERVICE OFFERING</h2>
<div class="abs cards">
  <div class="card"><svg viewBox="0 0 58 58" fill="none" stroke="#0a3fbf" stroke-width="2"><circle cx="28" cy="26" r="16"/><circle cx="28" cy="26" r="6"/><path d="M20 42v12M14 26H8"/></svg><h3>Research<br>Specialist</h3></div>
  <div class="card"><svg viewBox="0 0 58 58" fill="none" stroke="#0a3fbf" stroke-width="2"><circle cx="30" cy="16" r="10"/><path d="M4 38h10l14 6h14l12-8M4 52h12l14 4 24-14"/></svg><h3>Dedicated<br>Recruiter</h3></div>
  <div class="card"><svg viewBox="0 0 58 58" fill="none" stroke="#0a3fbf" stroke-width="2"><circle cx="32" cy="26" r="20"/><path d="M6 14l14 14-6 6 14 14"/><text x="26" y="30" font-size="13" fill="#0a3fbf" stroke="none" font-family="Montserrat">24</text></svg><h3>24/7<br>Sourcing</h3></div>
  <div class="card"><svg viewBox="0 0 58 58" fill="none" stroke="#0a3fbf" stroke-width="2"><circle cx="16" cy="16" r="11"/><path d="M24 24l10 10"/><rect x="12" y="40" width="7" height="16"/><rect x="26" y="30" width="7" height="26"/><rect x="40" y="18" width="7" height="38"/></svg><h3>On Demand<br>Recruitment</h3></div>
  <div class="card"><svg viewBox="0 0 58 58" fill="none" stroke="#0a3fbf" stroke-width="2"><circle cx="34" cy="24" r="18"/><circle cx="34" cy="20" r="6"/><path d="M24 36c4-6 16-6 20 0M20 38L4 54"/></svg><h3>Bench<br>Marketing</h3></div>
</div>

<section class="feature">
  <div class="abs frame" style="left:692px;top:1290px;width:455px;height:349px"></div>
  <div class="abs photo" style="left:656px;top:1253px;width:455px;height:351px;background:linear-gradient(135deg,#8a7a62,#c9b79c 55%,#e4ddd2)" role="img" aria-label="Recruiter interviewing a candidate at a café table"></div>
  <h2 class="abs section-title feature-title" style="left:88px;top:1248px">VALUES</h2>
  <p class="abs feature-text" style="left:89px;top:1314px">Lorem ipsum dolor sit amet, consectetur adipiscing elit, sed do eiusmod tempor incididunt ut labore et dolore magna aliqua. Ut enim ad minim veniam, quis nostrud exercitation ullamco laboris nisi ut aliquip ex ea commodo consequat. Duis aute irure dolor in reprehenderit in voluptate velit esse cillum dolore eu fugiat nulla pariatur. Excepteur sint occæcat cupidatat non proident, sunt in culpa qui officia deserunt mollit anim id est laborum.</p>
  <div class="abs btn" style="left:89px;top:1554px">READ MORE</div>
</section>

<section class="feature">
  <div class="abs frame" style="left:48px;top:1727px;width:455px;height:349px"></div>
  <div class="abs photo" style="left:89px;top:1691px;width:456px;height:350px;background:linear-gradient(180deg,#d8d6d2,#6a6d74 60%,#2c2f36)" role="img" aria-label="Group of smiling young professionals standing together"></div>
  <h2 class="abs section-title feature-title" style="left:584px;top:1686px">BENEFITS</h2>
  <p class="abs feature-text" style="left:585px;top:1752px">Lorem ipsum dolor sit amet, consectetur adipiscing elit, sed do eiusmod tempor incididunt ut labore et dolore magna aliqua. Ut enim ad minim veniam, quis nostrud exercitation ullamco laboris nisi ut aliquip ex ea commodo consequat. Duis aute irure dolor in reprehenderit in voluptate velit esse cillum dolore eu fugiat nulla pariatur. Excepteur sint occæcat cupidatat non proident, sunt in culpa qui officia deserunt mollit anim id est laborum.</p>
  <div class="abs btn" style="left:585px;top:1991px">READ MORE</div>
</section>

<footer class="abs footer">
  <div class="brand">CREWLINE</div>
  <nav class="abs footer-nav"><span>HOME</span><span>|</span><span>SERVICE</span><span>|</span><span>USER STORIES</span><span>|</span><span>ONSHORE/OFFSHORE</span><span>|</span><span>CONTACT</span></nav>
  <div class="abs social"><span></span><span></span><span></span><span></span></div>
  <p class="abs copy">Copyrights © The Company name 2020 | Allrights Reserved</p>
</footer>
</body>
</html>
```